Business Card Design

I'm a commercial general contractor remodel offices, hotels, health clubs and stores mostly San Francisco and the peninsula
the file I down loaded is kind of what I want I like the I beam with my company name in it, that would be fine with me but if you have better Idea will look at it you never know, I'm decided to give in and change my company name to how every one knows me, I have been in business since 1991, I like the I beam logo I included one of my old card from my old company for reference for you.

BROCK CONSTRUCTION (is my company name)
Warren Pelkey contractor, LIc 514387
3148 Larkspur Row, Harbor Vale, Oregon 94071
mobile, (415) 736-4052
phone (650) 514-2087
Fax, (650) 514-2088
email, brock@brockconstruction.example

```html
<!DOCTYPE html>
<html lang="en">
<head>
<meta charset="utf-8">
<title>Brock Construction – Business Card</title>
<link rel="stylesheet" href="https://fonts.googleapis.com/css2?family=Open+Sans:wght@300;400;600&display=swap">
<style>
  :root {
    --backdrop: #e9e4dc;
    --card-white: #fbfbfa;
    --maroon: #9a4c53;
    --maroon-dark: #7e3a41;
    --accent-orange: #ea9f2f;
    --text-light: #f6e9ea;
    --name-tone: #d8b5b8;
    --logo-ink: #6e2a31;
    --divider: rgba(255,255,255,0.35);
  }
  * { margin: 0; padding: 0; box-sizing: border-box; }
  html, body { width: 1200px; height: 1023px; overflow: hidden; }
  body {
    background: var(--backdrop);
    font-family: "Open Sans", Arial, sans-serif;
    position: relative;
  }
  .business-card {
    position: absolute;
    left: 75px; top: 211px;
    width: 1050px; height: 600px;
    background: var(--card-white);
    box-shadow: 0 10px 30px rgba(0,0,0,0.18);
    overflow: hidden;
  }
  .card-top {
    position: absolute; left: 0; top: 0; right: 0; height: 250px;
    background: linear-gradient(180deg, #ffffff, #f1f1ef);
  }
  .brand {
    position: absolute; left: 70px; top: 120px;
    display: flex; align-items: center; gap: 18px;
  }
  .brand-mark {
    width: 30px; height: 30px; background: var(--logo-ink);
  }
  .brand-name {
    font-weight: 600; font-size: 34px; letter-spacing: 3px;
    color: var(--logo-ink);
  }
  .accent-line {
    position: absolute; left: 0; right: 0; top: 250px; height: 6px;
    background: var(--accent-orange);
  }
  .card-band {
    position: absolute; left: 0; right: 0; top: 262px; bottom: 0;
    background: linear-gradient(180deg, var(--maroon), var(--maroon-dark));
    color: var(--text-light);
  }
  .holder-name {
    position: absolute; left: 70px; top: 38px;
    font-weight: 300; font-size: 40px; letter-spacing: 1px;
    color: var(--name-tone); text-transform: uppercase;
  }
  .contact-list { list-style: none; position: absolute; }
  .contact-list li {
    display: flex; align-items: flex-start; gap: 20px;
    font-size: 24px; font-weight: 300; line-height: 1.35;
    margin-bottom: 16px;
  }
  .contact-list svg { flex: none; width: 30px; height: 30px; margin-top: 2px; }
  .contact-left { left: 70px; top: 130px; }
  .divider {
    position: absolute; left: 690px; top: 40px; width: 1px; height: 250px;
    background: var(--divider);
  }
  .role {
    position: absolute; left: 730px; top: 40px;
    font-size: 30px; font-weight: 400; letter-spacing: 1px;
  }
  .contact-right { left: 730px; top: 110px; }
  .contact-right li { font-size: 26px; font-weight: 400; margin-bottom: 10px; }
</style>
</head>
<body>
  <article class="business-card">
    <div class="card-top">
      <div class="brand">
        <span class="brand-mark"></span>
        <span class="brand-name">BROCK CONSTRUCTION</span>
      </div>
    </div>
    <div class="accent-line"></div>
    <section class="card-band">
      <h1 class="holder-name">Warren Pelkey</h1>
      <ul class="contact-list contact-left">
        <li>
          <svg viewBox="0 0 30 30" fill="none" stroke="currentColor" stroke-width="1.8"><circle cx="15" cy="15" r="13"/><rect x="8" y="10" width="14" height="10"/><path d="M8 10l7 6 7-6"/></svg>
          <span>brock@brockconstruction.example</span>
        </li>
        <li>
          <svg viewBox="0 0 30 30" fill="none" stroke="currentColor" stroke-width="2"><path d="M15 28s-9-10-9-16a9 9 0 0 1 18 0c0 6-9 16-9 16z"/><circle cx="15" cy="12" r="3.5"/></svg>
          <span>Llc 514387, 3148 Larkspur Row<br>Harbor Vale, Oregon 94071</span>
        </li>
      </ul>
      <div class="divider"></div>
      <p class="role">CONTRACTOR</p>
      <ul class="contact-list contact-right">
        <li>
          <svg viewBox="0 0 30 30" fill="currentColor"><rect x="9" y="3" width="12" height="24" rx="2"/><rect x="11" y="6" width="8" height="15" fill="#9a4c53"/><circle cx="15" cy="24" r="1.3" fill="#9a4c53"/></svg>
          <span>(415) 736-4052</span>
        </li>
        <li>
          <svg viewBox="0 0 30 30" fill="none" stroke="currentColor" stroke-width="1.8"><circle cx="15" cy="15" r="13"/><path d="M10 8l3 0 1 4-2 1.5a9 9 0 0 0 4.5 4.5l1.5-2 4 1v3a2 2 0 0 1-2 2A12 12 0 0 1 8 10a2 2 0 0 1 2-2z" fill="currentColor" stroke="none"/></svg>
          <span>(650) 514-2087</span>
        </li>
        <li>
          <svg viewBox="0 0 30 30" fill="none" stroke="currentColor" stroke-width="1.8"><rect x="4" y="10" width="22" height="16" rx="1"/><rect x="9" y="4" width="12" height="8"/><path d="M8 16h6M8 20h6M18 16h4M18 20h4"/></svg>
          <span>(650) 514-2088</span>
        </li>
      </ul>
    </section>
  </article>
</body>
</html>
```